Business Card Design

We need a business card designed for our new company. Prefer a black card with white logo & writing.

Contact Information for Business Card

Ted Galloway, address: 7-4812 Fernhollow Road, Abbotsford, BC, V3K 8R2, Office Phone: 604-712-3390, Cell: 604-947-2164, Email: ted@resinworkshub.ca

Colors

Designer to choose only greyscale colors for use in the design.

```html
<!DOCTYPE html>
<html lang="en">
<head>
<meta charset="utf-8">
<title>Resin Works Hub – Business Card</title>
<link href="https://fonts.googleapis.com/css2?family=Poppins:wght@400;700&display=swap" rel="stylesheet">
<style>
  :root {
    --stage: #1d1d1d;
    --card-black: #1a1818;
    --card-grey: #4a4848;
    --accent-line: #8a8888;
    --pattern-tone: #221f1f;
    --ink: #ffffff;
  }
  html, body {
    margin: 0;
    width: 1200px;
    height: 1015px;
    overflow: hidden;
    background: var(--stage);
    font-family: "Poppins", sans-serif;
  }
  .stage {
    position: relative;
    width: 1200px;
    height: 1015px;
  }
  .card {
    position: absolute;
    left: 290px;
    width: 620px;
    height: 354px;
    border-radius: 4px;
    overflow: hidden;
    box-shadow: 0 12px 30px rgba(0,0,0,.55);
  }
  .card--back { top: 95px; background: var(--card-black); }
  .card--front { top: 560px; background: var(--card-grey); }

  .back-pattern {
    position: absolute;
    inset: 0;
    background: linear-gradient(135deg, var(--pattern-tone), var(--card-black));
  }
  .back-name {
    position: absolute;
    left: 0; right: 0; top: 162px;
    text-align: center;
    color: var(--ink);
    font-weight: 700;
    font-size: 18px;
    letter-spacing: 1px;
  }

  .front-shape { position: absolute; inset: 0; }
  .brand {
    position: absolute;
    left: 360px; top: 100px;
    width: 230px;
    color: var(--ink);
    font-weight: 700;
    font-size: 34px;
    line-height: 1.05;
    letter-spacing: 1px;
    text-align: center;
  }
  .contact {
    position: absolute;
    left: 52px; top: 92px;
    color: var(--ink);
  }
  .contact__name {
    margin: 0 0 36px;
    font-weight: 700;
    font-size: 22px;
    letter-spacing: 1px;
  }
  .contact__address {
    margin: 0 0 40px;
    font-size: 14.5px;
    line-height: 1.3;
  }
  .contact__list {
    list-style: none;
    margin: 0; padding: 0;
    font-size: 14.5px;
    line-height: 1.35;
  }
  .contact__list li { display: flex; align-items: center; gap: 8px; }
  .contact__list svg { width: 13px; height: 13px; flex: none; }
</style>
</head>
<body>
<main class="stage">

  <section class="card card--back" aria-label="Card back">
    <div class="back-pattern" role="img" aria-label="Faint repeating brand pattern across the card back"></div>
    <div class="back-name">RESIN WORKS HUB</div>
  </section>

  <section class="card card--front" aria-label="Card front">
    <svg class="front-shape" viewBox="0 0 620 354" aria-hidden="true">
      <polyline points="336,0 236,170 312,276 620,276" fill="none" stroke="var(--accent-line)" stroke-width="3"/>
      <polygon points="348,0 620,0 620,268 318,268 246,170" fill="var(--card-black)"/>
    </svg>

    <div class="brand">RESIN<br>WORKS HUB</div>

    <div class="contact">
      <h1 class="contact__name">TED GALLOWAY</h1>
      <p class="contact__address">7-4812 Fernhollow Road,<br>Abbotsford, BC, V3K 8R2</p>
      <ul class="contact__list">
        <li>
          <svg viewBox="0 0 16 16"><path d="M3 1.5l3 3-1.6 1.6a9 9 0 0 0 5.5 5.5L11.5 10l3 3-1.8 1.8C7 14.5 1.5 9 1.2 3.3z" fill="none" stroke="#fff" stroke-width="1.4"/></svg>
          604-712-3390
        </li>
        <li>
          <svg viewBox="0 0 16 16"><rect x="4" y="1" width="8" height="14" rx="1.5" fill="none" stroke="#fff" stroke-width="1.4"/><line x1="7" y1="12.5" x2="9" y2="12.5" stroke="#fff" stroke-width="1.4"/></svg>
          604-947-2164
        </li>
        <li>
          <svg viewBox="0 0 16 16"><rect x="1" y="3" width="14" height="10" fill="#fff"/><polyline points="1,3 8,9 15,3" fill="none" stroke="var(--card-grey)" stroke-width="1.3"/></svg>
          ted@resinworkshub.ca
        </li>
      </ul>
    </div>
  </section>

</main>
</body>
</html>
```